Namecard Designs+Logo for a High End Automobile Company

We need a new business card for our company called Nordel Motorwerk.

www.nordelmotorwerk.example.sg
Our new website will be up in 2.5 months time.

We sell used and brand new continental cars like Valcrest, KTR, Almira, Dunvale and etc. Currently we are operating from 2 offices in Singapore and United Kingdom.

We want a design which is serious. We are open to colours but try to keep it at a maximum of 3 colours.

We prefer something simple and minimal. We are open to 2 sides printing or even 2 sided namecards. Both UK and Singapore company offices address must be in; either side by side, front and back, or even 2 sided cards.

The logo can be a text logo, emblem, abstract, pictorial or combination.

We are printing with Printlyx.com so please kindly follow the printing guideline.

http://uk.printlyx.example/help/faq/templates-and-guidelines.html

Rich and Car Enthusiasts

Printing

• Our 2 offices; UK and Singapore.

Our slogan which is " The Automobile Specialist"
• Not more than 3 colours

```html
<!DOCTYPE html>
<html lang="en">
<head>
<meta charset="utf-8">
<title>Nordel Motorwerk – Logo and Business Card</title>
<link rel="stylesheet" href="https://fonts.googleapis.com/css2?family=Archivo+Black&family=Arimo:wght@400;700&display=swap">
<style>
  :root {
    --board: #2f2f31;
    --label: #ffffff;
    --paper: #ffffff;
    --brand-blue: #1f6fc4;
    --brand-blue-light: #4aa3e6;
    --ink-grey: #5a5a5a;
    --silver: #c9cbce;
    --silver-dark: #9a9da2;
    --shadow: rgba(0,0,0,0.45);
  }
  * { margin: 0; padding: 0; box-sizing: border-box; }
  html, body { width: 1200px; height: 900px; overflow: hidden; }
  body { background: var(--board); position: relative; font-family: "Arimo", Arial, sans-serif; }

  .board-label {
    position: absolute; left: 37px; top: 22px;
    font-family: "Archivo Black", Arial, sans-serif;
    font-size: 29px; color: var(--label); letter-spacing: 1px;
  }

  .logo-tile {
    position: absolute; left: 37px; top: 82px; width: 305px; height: 300px;
    background: var(--paper); box-shadow: 0 4px 14px var(--shadow);
    display: flex; flex-direction: column; align-items: center; justify-content: center; gap: 22px;
  }
  .brand-dot {
    border-radius: 50%;
    background: radial-gradient(circle at 40% 35%, var(--brand-blue-light), var(--brand-blue));
  }
  .logo-tile .brand-dot { width: 150px; height: 150px; }
  .brand-name {
    font-family: "Arimo", Arial, sans-serif; font-weight: 700;
    color: var(--brand-blue); white-space: nowrap;
  }
  .logo-tile .brand-name { font-size: 30px; }
  .slogan {
    font-size: 13px; color: var(--ink-grey); letter-spacing: 1.5px;
    text-transform: uppercase; white-space: nowrap; margin-top: -8px;
  }

  .card {
    position: absolute; background: var(--paper); overflow: hidden;
    box-shadow: 0 5px 16px var(--shadow);
  }
  .card svg.swoosh { position: absolute; inset: 0; width: 100%; height: 100%; }

  .card-front { left: 450px; top: 85px; width: 672px; height: 365px; }
  .card-front .brand-lockup {
    position: absolute; left: 28px; top: 28px;
    display: flex; flex-direction: column; align-items: center; gap: 12px;
  }
  .card-front .brand-dot { width: 110px; height: 110px; }
  .card-front .brand-name { font-size: 22px; }
  .card-front .slogan { font-size: 11px; margin-top: -6px; }

  .person { position: absolute; right: 30px; top: 30px; text-align: right; }
  .person-name { font-size: 29px; font-weight: 700; color: var(--brand-blue); }
  .person-role { font-size: 20px; font-weight: 700; color: var(--ink-grey); margin-top: 2px; }

  .contact-list {
    position: absolute; right: 24px; top: 112px; list-style: none;
    font-size: 15.5px; color: var(--ink-grey); line-height: 19px; text-align: right;
  }
  .contact-list li { display: flex; justify-content: flex-end; align-items: center; gap: 8px; }
  .contact-list li.spaced { letter-spacing: 1.4px; }
  .contact-list li.office-label { font-weight: 700; color: var(--brand-blue); font-size: 12px; letter-spacing: 1.5px; }
  .contact-list li.gap-before { margin-top: 5px; }
  .contact-list svg { width: 14px; height: 14px; flex: none; }
  .icon-fill { fill: var(--brand-blue); }
  .icon-line { fill: none; stroke: var(--brand-blue); stroke-width: 1.6; }

  .card-back { left: 300px; top: 517px; width: 640px; height: 345px; }
  .card-back .brand-lockup {
    position: absolute; left: 0; right: 0; top: 62px;
    display: flex; flex-direction: column; align-items: center; gap: 16px;
  }
  .card-back .brand-dot { width: 150px; height: 150px; }
  .card-back .brand-name { font-size: 26px; }
</style>
</head>
<body>

  <h1 class="board-label">LOGO DESIGNED</h1>

  <section class="logo-tile" aria-label="Nordel Motorwerk logo">
    <span class="brand-dot"></span>
    <span class="brand-name">Nordel Motorwerk</span>
  </section>

  <article class="card card-front" aria-label="Business card front">
    <svg class="swoosh" viewBox="0 0 672 365" preserveAspectRatio="none" aria-hidden="true">
      <defs>
        <linearGradient id="frontBlue" x1="0" y1="0" x2="1" y2="0">
          <stop offset="0" stop-color="var(--brand-blue)"/>
          <stop offset="1" stop-color="var(--brand-blue-light)"/>
        </linearGradient>
        <linearGradient id="frontSilver" x1="0" y1="0" x2="1" y2="0">
          <stop offset="0" stop-color="var(--silver-dark)"/>
          <stop offset="0.5" stop-color="#e8e9eb"/>
          <stop offset="1" stop-color="var(--silver)"/>
        </linearGradient>
      </defs>
      <path d="M0 250 C180 290 380 330 672 345 L672 365 L0 365 Z" fill="url(#frontSilver)"/>
      <path d="M0 290 C200 310 420 335 620 350 C500 352 300 345 0 330 Z" fill="#ffffff"/>
      <path d="M0 300 C220 320 420 340 640 358 L640 365 L0 365 Z" fill="url(#frontBlue)"/>
      <path d="M520 365 C600 345 640 320 672 300 L672 365 Z" fill="url(#frontBlue)"/>
    </svg>

    <div class="brand-lockup">
      <span class="brand-dot"></span>
      <span class="brand-name">Nordel Motorwerk</span>
      <span class="slogan">The Automobile Specialist</span>
    </div>

    <div class="person">
      <p class="person-name">Liam Harcourt</p>
      <p class="person-role">Principal</p>
    </div>

    <ul class="contact-list">
      <li class="spaced">18 Kestrel Quay Road
        <svg viewBox="0 0 14 14"><path class="icon-line" d="M2 7 L7 2 L12 7 M3.5 6 V12 H10.5 V6"/></svg></li>
      <li class="spaced">Marlow Bay, SG 408562
        <svg viewBox="0 0 14 14"></svg></li>
      <li class="spaced">42 Harrowgate Lane
        <svg viewBox="0 0 14 14"><path class="icon-line" d="M2 7 L7 2 L12 7 M3.5 6 V12 H10.5 V6"/></svg></li>
      <li class="spaced">Kensford, UK KN8 4QX
        <svg viewBox="0 0 14 14"></svg></li>
      <li class="gap-before">liam@nordelmotorwerk.example.sg
        <svg viewBox="0 0 14 14"><rect class="icon-fill" x="1" y="3" width="12" height="8" rx="1"/></svg></li>
      <li>www.nordelmotorwerk.example.sg
        <svg viewBox="0 0 14 14"><circle class="icon-line" cx="7" cy="7" r="5.5"/></svg></li>
      <li class="spaced">604-555-0148
        <svg viewBox="0 0 14 14"><path class="icon-fill" d="M1 5 Q7 1 13 5 L11 7 L9 5.5 H5 L3 7 Z M3 8 H11 V12 H3 Z"/></svg></li>
      <li class="spaced">604-555-0172
        <svg viewBox="0 0 14 14"><rect class="icon-line" x="2" y="2" width="10" height="10"/></svg></li>
      <li class="spaced">604-555-0193
        <svg viewBox="0 0 14 14"><rect class="icon-fill" x="4" y="1" width="6" height="12" rx="1"/></svg></li>
    </ul>
  </article>

  <article class="card card-back" aria-label="Business card back">
    <svg class="swoosh" viewBox="0 0 640 345" preserveAspectRatio="none" aria-hidden="true">
      <defs>
        <linearGradient id="backBlue" x1="0" y1="0" x2="1" y2="0">
          <stop offset="0" stop-color="var(--brand-blue)"/>
          <stop offset="0.5" stop-color="var(--brand-blue-light)"/>
          <stop offset="1" stop-color="var(--brand-blue)"/>
        </linearGradient>
        <linearGradient id="backSilver" x1="0" y1="0" x2="1" y2="0">
          <stop offset="0" stop-color="var(--silver-dark)"/>
          <stop offset="0.5" stop-color="#eeeff0"/>
          <stop offset="1" stop-color="var(--silver-dark)"/>
        </linearGradient>
      </defs>
      <path d="M0 0 H640 V45 C460 20 200 15 0 95 Z" fill="url(#backBlue)"/>
      <path d="M0 95 C200 15 460 20 640 45 V62 C460 38 220 40 0 120 Z" fill="url(#backSilver)"/>
      <path d="M640 345 H0 V300 C180 325 440 330 640 250 Z" fill="url(#backBlue)"/>
      <path d="M640 250 C440 330 180 325 0 300 V283 C180 305 420 305 640 225 Z" fill="url(#backSilver)"/>
    </svg>

    <div class="brand-lockup">
      <span class="brand-dot"></span>
      <span class="brand-name">Nordel Motorwerk</span>
      <span class="slogan">The Automobile Specialist</span>
    </div>
  </article>

</body>
</html>
```